Vesta PR Website

Vesta PR are a PR company with a requirement for a new website. In consultation with the client, we have defined a wireframe for a homepage to show content and functionality. A PDF of the wire frame is attached.
Current site http://www.vesta-pr.co.uk/
Updates
If you are using Stock Photography - please use iStock
Dear All
Unfortunately, my client didn't like any of the designs submitted.
I've uploaded 3 examples of the type of photography that will appear in the carousel as supplied by the client.
Target Market(s)
Business to Business/Professionals - high value clients
Number of Pages Required
1 page
Requirements
Must have
- Colour scheme is attached as a .ase file from Kuler and can be viewed on Kuler if you search for 'VESTA PR Palette'
Corporate Typeface is Futura Book - use of Cufon is OK
Current Logo to be reatainedCall 2 Action Buttons will be controlled via the CMS so a generic background may be useful for these.
Nice to have
- RSS feeds

```html
<!DOCTYPE html>
<html lang="en">
<head>
<meta charset="utf-8">
<title>Vesta PR — Home</title>
<link href="https://fonts.googleapis.com/css2?family=Jost:wght@400;500&family=Arimo:wght@400;700&display=swap" rel="stylesheet">
<style>
:root{
  --page-bg:#ebebeb;
  --white:#ffffff;
  --panel-light:#f4f4f4;
  --teal:#8dd6cc;
  --teal-dark:#64ab9f;
  --heading:#3f6b58;
  --heading-soft:#6bb09a;
  --footer:#7ab5a4;
  --footer-box:#93c3b5;
  --footer-bar:#4a6a55;
  --text:#333333;
  --call-blue:#1e8bcc;
}
*{box-sizing:border-box;margin:0;padding:0}
html,body{width:960px;height:1200px;overflow:hidden}
body{background:var(--page-bg);font-family:"Arimo",Arial,sans-serif;color:var(--text);position:relative}
a{color:inherit;text-decoration:none}
.abs{position:absolute}

.social-strip{left:525px;top:0;width:340px;height:28px;background:#e0e0e0;border-radius:0 0 6px 6px;display:flex;align-items:center;justify-content:space-around;font-size:9px;color:#777}
.social-strip a{display:flex;align-items:center;gap:5px;text-decoration:underline}
.social-strip .dot{width:14px;height:14px;border-radius:3px;background:#b9b9b9}
.social-strip .dot.mail{background:#9ccc5a}
.social-strip .sep{width:1px;height:16px;background:#c4c4c4}

.page{left:98px;top:40px;width:768px;height:1032px;background:var(--white)}
.logo{left:132px;top:72px;font-family:"Jost",sans-serif;font-weight:400;font-size:22px;line-height:28px;color:#222}
.call{right:112px;top:72px;font-family:"Jost",sans-serif;font-size:14px;color:#a5a5a5}
.call strong{font-weight:400;font-size:22px;color:var(--call-blue);letter-spacing:.5px}

.main-nav{left:96px;top:132px;width:769px;height:30px;background:linear-gradient(#8ad0c5,#72bfb2);display:flex;align-items:center;padding-left:24px;box-shadow:0 3px 4px rgba(0,0,0,.12)}
.main-nav a{font-size:10.5px;color:#fff;padding:0 14px;border-right:1px solid rgba(255,255,255,.25);line-height:30px;white-space:nowrap}
.main-nav a.current{color:#3c3c3c}
.main-nav a:last-child{border:none}

.hero{left:117px;top:182px;width:726px;height:208px;background:#e9e9e9}
.service-menu{left:120px;top:186px;width:175px;height:200px;list-style:none}
.service-menu li{height:38.4px;font-size:11px;color:#111;padding:0 20px;display:flex;align-items:center}
.service-menu li.active{background:var(--teal);color:#fff;height:27px;margin:10px 0 2px}
.banner{left:295px;top:186px;width:546px;height:200px;background:var(--teal);overflow:hidden}
.banner h2{position:absolute;left:39px;top:36px;font-family:"Jost",sans-serif;font-weight:400;font-size:21px;line-height:24px;color:#3d4a48;letter-spacing:.5px}
.banner .cta{position:absolute;left:41px;top:108px;width:239px;height:55px;background:#7fd0c4;display:flex;align-items:center;justify-content:space-between;padding:0 16px 0 14px;font-family:"Jost",sans-serif;color:#fff;font-size:13px;line-height:19px}
.banner .cta span{text-decoration:underline}
.banner .photo{position:absolute;left:313px;top:0;width:233px;height:200px;background:linear-gradient(135deg,#8dd6cc 0%,#e28a86 45%,#d34f4f 100%)}

.intro{left:114px;top:410px;width:480px;height:290px;background:#fff;box-shadow:0 0 6px rgba(0,0,0,.04)}
.intro h1{position:absolute;left:19px;top:16px;font-family:"Jost",sans-serif;font-weight:400;font-size:19.5px;color:var(--heading);letter-spacing:.5px}
.intro .body{position:absolute;left:19px;top:56px;width:450px;font-size:9.6px;line-height:19.2px;letter-spacing:.4px;white-space:nowrap}
.intro .body p{margin-bottom:19.2px}

.news-box{top:722px;width:231px;height:145px;background:var(--panel-light)}
.news-box h3{position:absolute;left:15px;top:10px;font-family:"Jost",sans-serif;font-weight:400;font-size:17px;color:var(--heading-soft);letter-spacing:.5px}
.news-box .rule{position:absolute;left:14px;right:14px;top:35px;height:1px;background:#dedede}
.news-box p{position:absolute;left:15px;top:46px;font-size:9px;line-height:14.4px;letter-spacing:.5px;color:#444;white-space:nowrap}
.news-box .more{position:absolute;left:15px;font-size:8px;color:var(--heading-soft);text-decoration:underline}
.rss{position:absolute;right:15px;top:13px}
.shell{position:absolute;left:128px;top:49px;width:87px;height:66px;background:linear-gradient(135deg,#5fa6d8,#b7dc9f 60%,#4d8c8a)}

.sidebar{left:606px;top:412px;width:234px;height:455px;background:#fff}
.c2a{left:626px;width:199px;height:97px}
.c2a .bar{height:25px;background:var(--teal-dark);color:#fff;font-size:10.5px;display:flex;align-items:center;justify-content:space-between;padding:0 7px}
.c2a.light .bar{background:#efefef;color:#2e5a48}
.c2a .img{height:72px;position:relative}
.c2a .label{position:absolute;left:0;background:rgba(255,255,255,.85);font-family:"Jost",sans-serif;font-size:14px;line-height:19px;color:#333;padding:2px 6px;letter-spacing:.5px}

.footer{left:98px;top:910px;width:768px;height:144px;background:var(--footer)}
.foot-links{top:930px;list-style:none;font-size:9.8px;color:#fff;line-height:19.2px}
.enews{left:625px;top:930px;width:209px;height:108px;background:var(--footer-box)}
.enews h4{position:absolute;left:9px;top:8px;font-family:"Jost",sans-serif;font-weight:400;font-size:13.5px;color:#fff;letter-spacing:.5px}
.enews .field{position:absolute;left:10px;top:40px;width:190px;height:19px;background:#f2f2f2;border:1px solid #c9c9c9;font-size:8px;color:#666;padding:4px 7px}
.enews .btn{position:absolute;left:10px;top:76px;width:78px;height:24px;background:#a8e1d9;border-radius:3px;color:#fff;font-size:9.5px;display:flex;align-items:center;justify-content:center}
.footer-bar{left:98px;top:1054px;width:768px;height:18px;background:var(--footer-bar);font-size:7.6px;color:#fff;font-weight:700;display:flex;align-items:center;justify-content:space-between;padding:0 26px 0 6px;white-space:nowrap}
.footer-bar .here{color:var(--teal);font-weight:400}
.footer-bar .copy{font-weight:400}
</style>
</head>
<body>

<nav class="abs social-strip" aria-label="Contact links">
  <a href="#"><span class="dot mail"></span>Email Us</a><span class="sep"></span>
  <a href="#"><span class="dot"></span>Callwave</a><span class="sep"></span>
  <a href="#"><span class="dot"></span>Chirper</a><span class="sep"></span>
  <a href="#"><span class="dot"></span>Facepage</a>
</nav>

<div class="abs page"></div>

<div class="abs logo">Vesta PR</div>
<div class="abs call">Call us now <strong>0141 555 0190</strong></div>

<nav class="abs main-nav">
  <a class="current" href="#">Home</a><a href="#">Vesta Services</a><a href="#">Press Office</a><a href="#">Vesta Case Studies</a><a href="#">Vesta People</a><a href="#">Blog</a><a href="#">Vesta News</a><a href="#">Contact us</a>
</nav>

<div class="abs hero"></div>
<ul class="abs service-menu">
  <li class="active">Online Public Relations</li>
  <li>Media Relations</li>
  <li>Consumer Campaigns</li>
  <li>Crisis Public Relations</li>
  <li>Internal Communications</li>
</ul>
<section class="abs banner">
  <svg class="abs" width="546" height="200" style="left:0;top:0" aria-hidden="true">
    <path d="M150 0 Q260 90 330 200 L380 200 Q300 80 220 0Z" fill="#a8e0d8" opacity=".6"/>
    <path d="M0 120 Q10 170 30 200 L60 200 Q30 150 20 100Z" fill="#a8e0d8" opacity=".6"/>
  </svg>
  <h2>Orem ipsum dolor sit amet<br>conse adipiscing elit.</h2>
  <a class="cta" href="#"><span>Orem ipsum dolor sit amet<br>conse adipiscing elit.</span>
    <svg width="27" height="27" viewBox="0 0 27 27"><circle cx="13.5" cy="13.5" r="13.5" fill="#222"/><path d="M7 13.5h11M13 8l5.5 5.5L13 19" stroke="#fff" stroke-width="3" fill="none"/></svg></a>
  <div class="photo" role="img" aria-label="Red letter tiles spelling innovation, strategy and success"></div>
</section>

<article class="abs intro">
  <h1>Introduction h1</h1>
  <div class="body">
    <p>Lorem ipsum dolor sit amet, consectetur adipiscing elit. Etiam bibendum posuere justo a<br>lectus neque, pharetra a faucibus vel, vestibulum sed massa. Cum sociis natoque penati<br>dis parturient montes, nascetur ridiculus mus. Nulla accumsan diam diam. Praesent non<br>odio blandit viverra non vitae magna.</p>
    <p>haretra a faucibus vel, vestibulum sed massa. Cum sociis natoque penatibus et magnis<br>dis parturient montes, nascetur ridiculus mus. Nulla accumsan diam diam. Praesent non<br>odio blandit.</p>
    <p>us vel, vestibulum sed massa. Cum sociis natoque penatibus et magnis<br>dis parturient montes, nascetur.</p>
  </div>
</article>

<section class="abs news-box" style="left:119px">
  <h3>Client News</h3>
  <svg class="rss" width="16" height="16" viewBox="0 0 16 16" aria-label="RSS"><rect width="16" height="16" rx="2" fill="#f08a24"/><circle cx="4.5" cy="11.5" r="1.7" fill="#fff"/><path d="M3 7a6 6 0 0 1 6 6M3 3.5a9.5 9.5 0 0 1 9.5 9.5" stroke="#fff" stroke-width="1.8" fill="none"/></svg>
  <div class="rule"></div>
  <p>Gismod, mauris vel biben du mfturingilla,<br>fringilla, metutus dui vi fringilla, a artucu,<br>vitae eleiffringilla.</p>
  <a class="more" href="#" style="top:99px">read more</a>
</section>

<section class="abs news-box" style="left:364px">
  <h3>Blog Entry</h3>
  <div class="rule"></div>
  <p>Gismod, mauris vel<br>en du mfturingilla,<br>fringilla, metutus dui<br>ringilla, a artucu, vita<br>e eleiffringilla.</p>
  <div class="shell" role="img" aria-label="Spiral sea shell"></div>
  <a class="more" href="#" style="top:128px">read more</a>
</section>

<aside class="abs sidebar"></aside>
<div class="abs c2a" style="top:430px">
  <div class="bar">C2A Button<svg width="14" height="14" viewBox="0 0 14 14"><circle cx="7" cy="7" r="7" fill="#fff"/><path d="M3.5 7h6M7 4l3 3-3 3" stroke="#64ab9f" stroke-width="1.8" fill="none"/></svg></div>
  <div class="img" role="img" aria-label="Desk calendar with red binding" style="background:linear-gradient(90deg,#c94a44,#eeeeee 40%,#dddddd)"><span class="label" style="top:14px">Lorem ipsum dolor</span></div>
</div>
<div class="abs c2a" style="top:538px">
  <div class="bar">C2A Button<svg width="14" height="14" viewBox="0 0 14 14"><circle cx="7" cy="7" r="7" fill="#fff"/><path d="M3.5 7h6M7 4l3 3-3 3" stroke="#64ab9f" stroke-width="1.8" fill="none"/></svg></div>
  <div class="img" role="img" aria-label="Black and white business portrait" style="background:linear-gradient(90deg,#f4f4f4,#bdbdbd 60%,#6e6e6e)"><span class="label" style="top:14px">Mexm ipsum ds<br>egaset, consedawed</span></div>
</div>
<div class="abs c2a" style="top:645px">
  <div class="bar">C2A Button<svg width="14" height="14" viewBox="0 0 14 14"><circle cx="7" cy="7" r="7" fill="#fff"/><path d="M3.5 7h6M7 4l3 3-3 3" stroke="#64ab9f" stroke-width="1.8" fill="none"/></svg></div>
  <div class="img" role="img" aria-label="Red letter tiles crossword" style="background:linear-gradient(135deg,#d96a66,#d34f4f 60%,#e8e8e8)"><span class="label" style="top:13px">Dssd dff dfae ed</span></div>
</div>
<div class="abs c2a light" style="top:753px">
  <div class="bar">C2A Button<svg width="14" height="14" viewBox="0 0 14 14"><circle cx="7" cy="7" r="7" fill="#64ab9f"/><path d="M3.5 7h6M7 4l3 3-3 3" stroke="#fff" stroke-width="1.8" fill="none"/></svg></div>
  <div class="img" role="img" aria-label="Businessman sketching a plan" style="background:linear-gradient(90deg,#f3ede6,#e6c2a6 40%,#f5f5f5)"><span class="label" style="top:20px;left:-2px">Ddolorit amet</span></div>
</div>

<footer class="abs footer"></footer>
<ul class="abs foot-links" style="left:119px">
  <li>Online Public Relations</li><li>Media Relations</li><li>Consumer Campagns</li><li>Crisis Public Relations</li><li>Internal Communications</li>
</ul>
<ul class="abs foot-links" style="left:274px">
  <li>Subscribe to RSS Feed</li><li>Our Facepage page</li><li>Link Three</li><li>Link Four</li>
</ul>
<form class="abs enews">
  <h4>Enews Sign-up</h4>
  <div class="field">Email Address</div>
  <div class="btn">Subscribe</div>
</form>
<div class="abs footer-bar">
  <span><span class="here">Home</span> | Vesta Services | Press Office | Vesta Case Studies | Vesta People | Blog | Vesta News | &nbsp;Contact us</span>
  <span class="copy">© 2010 Vesta PR All Rights Reserved</span>
</div>

</body>
</html>
```